Preschool Website

Looking to have a one page splash with a contact us form that uses some kind of verification to keep bots from filling out the form. We would like for it to be dynamic for both mobile and desktop. Would like to have it show up in search engines for preschool in are area. Would like to include a link to the website are current parents use for payment information.

Target Market(s)

Young Adults with Childrens

Industry/Entity Type

Preschool

Coding

Coded - Design and coding required

Number of Pages Required

1 page

Colors

Designer to choose colors to be used in the design.

Requirements
Must have
• Searchable in Quorla
• Contact us form
• Name
• Phone
• Email
• Message box
• Form must have code entered to submit to prevent junk emails
• Link to the website we use for parents to make payments
• our phone and address clickable on device to make call or map on phone
Should not have
• more then one page

```html
<!DOCTYPE html>
<html lang="en">
<head>
<meta charset="utf-8">
<title>Pebblewood Preschool – Contact</title>
<link rel="stylesheet" href="https://fonts.googleapis.com/css2?family=Baloo+2:wght@700;800&family=Poppins:wght@400;500;600&display=swap">
<style>
  :root {
    --green: #14d88f;
    --magenta: #cc0ea0;
    --panel: #d6d6d6;
    --white: #ffffff;
    --hero-dark: #5f5c58;
    --hero-mid: #77716a;
    --hero-wood: #6a5846;
    --illus-light: #f2c6e6;
    --illus-deep: #b0168c;
  }
  * { box-sizing: border-box; margin: 0; padding: 0; }
  html, body { width: 1093px; height: 1200px; overflow: hidden; background: var(--white); }
  body { position: relative; font-family: "Poppins", sans-serif; }

  .bar { position: absolute; left: 0; width: 100%; height: 6px; background: var(--green); z-index: 5; }
  .bar--top { top: 0; }
  .bar--bottom { bottom: 0; }

  .hero { position: absolute; left: 0; top: 0; width: 1093px; height: 647px; overflow: hidden; }
  .hero__backdrop {
    position: absolute; inset: 0;
    background: linear-gradient(180deg, var(--hero-dark) 0%, var(--hero-mid) 55%, var(--hero-wood) 100%);
  }

  .brand-name {
    position: absolute; left: 90px; top: 30px;
    font-family: "Baloo 2", sans-serif; font-weight: 800; font-size: 36px; line-height: 1.2;
    color: var(--green);
  }

  .contact-form {
    position: absolute; left: 90px; top: 102px; width: 322px; height: 523px;
    background: var(--panel); border-radius: 10px;
    box-shadow: 0 2px 6px rgba(0,0,0,.25);
  }
  .field {
    position: absolute; left: 24px; width: 273px; height: 37px;
    background: var(--white); border-radius: 10px;
    box-shadow: 0 2px 3px rgba(0,0,0,.3);
    padding: 8px 0 0 33px;
    font-size: 16px; color: var(--green);
  }
  .field--name { top: 31px; }
  .field--phone { top: 95px; }
  .field--email { top: 159px; }
  .field--code { top: 222px; }
  .field--message { top: 286px; height: 146px; }
  .contact-form__submit {
    position: absolute; left: 169px; top: 457px; width: 128px; height: 41px;
    background: var(--magenta); border-radius: 9px;
    color: var(--white); font-size: 16px; font-weight: 500;
    display: flex; align-items: center; justify-content: center;
  }

  .hero__intro { position: absolute; left: 571px; top: 246px; width: 440px; color: var(--white); }
  .hero__title {
    font-family: "Baloo 2", sans-serif; font-weight: 800; font-size: 41px;
    color: var(--green); line-height: 1.15; margin-bottom: 4px; white-space: nowrap;
  }
  .hero__text { font-size: 16.4px; line-height: 23px; }

  .touch { position: absolute; left: 0; top: 647px; width: 100%; }
  .touch__title {
    position: absolute; top: 70px; width: 100%; text-align: center;
    font-family: "Baloo 2", sans-serif; font-weight: 800; font-size: 40px;
    color: var(--magenta);
  }
  .touch__art {
    position: absolute; top: 177px; width: 200px; height: 190px; border-radius: 48%;
    background: radial-gradient(circle at 50% 50%, var(--illus-deep) 0%, var(--magenta) 35%, var(--illus-light) 70%, rgba(242,198,230,0) 100%);
  }
  .touch__link {
    position: absolute; top: 393px; width: 255px; height: 55px;
    background: var(--magenta); border-radius: 9px;
    color: var(--white); font-size: 17px; font-weight: 600;
    display: flex; align-items: center; justify-content: center;
  }
  .col-1 { left: 123px; }
  .col-2 { left: 419px; }
  .col-3 { left: 715px; }
  .touch__art.col-1 { left: 150px; }
  .touch__art.col-2 { left: 447px; }
  .touch__art.col-3 { left: 743px; }
</style>
</head>
<body>
  <div class="bar bar--top"></div>

  <header class="hero">
    <div class="hero__backdrop" role="img" aria-label="Soft classroom photo with stacked books, coloured pencils and alphabet blocks on a desk"></div>

    <div class="brand-name">Pebblewood</div>

    <form class="contact-form">
      <div class="field field--name">Your Name</div>
      <div class="field field--phone">Your Phone</div>
      <div class="field field--email">Your Email</div>
      <div class="field field--code">Enter Your Code</div>
      <div class="field field--message">Your Message</div>
      <div class="contact-form__submit">Contact Us</div>
    </form>

    <div class="hero__intro">
      <h1 class="hero__title">Communication is key</h1>
      <p class="hero__text">Lorem ipsum dolor sit amet, consectetur adipisicing elit, sed do eiusmod tempor incididunt ut labore et dolore magna aliqua. Ut enim ad minim veniam, quis nostrud exercitation ullamco laboris nisi ut aliquip.</p>
    </div>
  </header>

  <section class="touch">
    <h2 class="touch__title">Get In Touch</h2>

    <div class="touch__art col-1" role="img" aria-label="Illustration of a hand holding a smartphone with a contact card"></div>
    <div class="touch__art col-2" role="img" aria-label="Illustration of a folded map with a location pin"></div>
    <div class="touch__art col-3" role="img" aria-label="Illustration of a hand paying with a card at a terminal"></div>

    <div class="touch__link col-1">Get Our Number</div>
    <div class="touch__link col-2">View Our Addres</div>
    <div class="touch__link col-3">Make Your Payment</div>
  </section>

  <div class="bar bar--bottom"></div>
</body>
</html>
```